Lumavento business card

We need a modern business card - With our 4 colors - See web: www.lumavento.dk

I have attached logo and som old business Cards we have - Lets Make the new ones shine...:-) -

Industry/Entity Type

Business

Requirements
Must have
• the logo with lumavento only,

```html
<!DOCTYPE html>
<html lang="da">
<head>
<meta charset="utf-8">
<title>Lumavento – visitkort</title>
<link href="https://fonts.googleapis.com/css2?family=Questrial&display=swap" rel="stylesheet">
<style>
  :root {
    --stage: #2b2b2c;
    --stage-edge: #121213;
    --card: #1f2022;
    --lime: #9fcb3a;
    --ink: #e9e9e9;
    --ink-soft: #c9c9c9;
    --rule: #dcdcdc;
  }
  * { margin: 0; padding: 0; box-sizing: border-box; }
  html, body { width: 1200px; height: 1189px; overflow: hidden; }
  body {
    background: radial-gradient(ellipse at 40% 30%, var(--stage), var(--stage-edge));
    font-family: "Questrial", sans-serif;
    color: var(--ink);
    position: relative;
  }
  .card {
    position: absolute;
    left: 160px;
    width: 880px;
    height: 500px;
    background: var(--card);
    border-radius: 28px;
    box-shadow: 0 18px 40px rgba(0,0,0,.55);
    overflow: hidden;
  }
  .card--front { top: 60px; }
  .card--back { top: 630px; }

  /* shared brand block */
  .brand-name {
    font-size: 34px;
    letter-spacing: 8px;
    color: var(--ink);
    display: flex;
    align-items: center;
    justify-content: center;
    gap: 12px;
    white-space: nowrap;
  }
  .brand-dot {
    width: 16px; height: 16px;
    border-radius: 50%;
    background: var(--lime);
  }
  .brand-rule {
    height: 2px;
    background: var(--lime);
    margin: 18px auto 14px;
  }
  .brand-tagline {
    text-align: center;
    color: var(--ink-soft);
    white-space: nowrap;
  }

  /* front */
  .card--front .brand { position: absolute; left: 280px; top: 196px; width: 320px; }
  .card--front .brand-rule { width: 280px; }
  .card--front .brand-tagline { font-size: 19px; }
  .front-footer {
    position: absolute;
    left: 0; top: 376px; width: 880px;
    display: flex; align-items: center; gap: 20px;
  }
  .front-rule { flex: 1; height: 2px; background: var(--lime); }
  .front-url { font-size: 22px; letter-spacing: .5px; white-space: nowrap; }

  /* back */
  .card--back .brand { position: absolute; left: 80px; top: 218px; width: 380px; }
  .card--back .brand-rule { width: 380px; }
  .card--back .brand-tagline { font-size: 22px; }
  .divider {
    position: absolute;
    left: 500px; top: 70px;
    width: 1px; height: 360px;
    background: var(--rule);
  }
  .contact {
    position: absolute;
    left: 540px; top: 80px;
    font-size: 23px;
    line-height: 1.25;
    white-space: nowrap;
  }
  .contact-name { color: var(--lime); font-size: 30px; line-height: 1; }
  .contact-title { margin-bottom: 28px; }
  .contact-address { margin-bottom: 12px; }
  .contact-line { display: flex; align-items: center; gap: 12px; margin-bottom: 4px; }
  .icon {
    width: 26px; height: 26px;
    border-radius: 4px;
    background: var(--lime);
    display: flex; align-items: center; justify-content: center;
  }
  .contact-web { color: var(--lime); margin-top: 14px; }
</style>
</head>
<body>
  <section class="card card--front" aria-label="Forside">
    <div class="brand">
      <div class="brand-name"><span class="brand-dot"></span>lumavento</div>
      <div class="brand-rule"></div>
      <p class="brand-tagline">Lys til hverdag</p>
    </div>
    <div class="front-footer">
      <span class="front-rule"></span>
      <p class="front-url">www.lumavento.dk</p>
      <span class="front-rule"></span>
    </div>
  </section>

  <section class="card card--back" aria-label="Bagside">
    <div class="brand">
      <div class="brand-name"><span class="brand-dot"></span>lumavento</div>
      <div class="brand-rule"></div>
      <p class="brand-tagline">Lys til hverdag</p>
    </div>
    <div class="divider"></div>
    <div class="contact">
      <p class="contact-name">Mikkel Aalbæk</p>
      <p class="contact-title">Salgsdirektør</p>
      <p class="contact-address">Solsikkevej 14<br>2300 København S</p>
      <p class="contact-line">
        <span class="icon"><svg width="14" height="18" viewBox="0 0 14 18"><rect x="1.5" y="1" width="11" height="16" rx="2" fill="none" stroke="#1f2022" stroke-width="2"/><rect x="4" y="4" width="6" height="5" fill="#1f2022"/></svg></span>
        +45 61 72 83 94
      </p>
      <p class="contact-line">
        <span class="icon"><svg width="16" height="16" viewBox="0 0 16 16"><path d="M3 1l3 3-2 2c1 2 3 4 5 5l2-2 3 3-2 3C7 15 1 9 0 4z" fill="#1f2022"/></svg></span>
        +45 32 47 19 06
      </p>
      <p class="contact-line">
        <span class="icon"><svg width="18" height="14" viewBox="0 0 18 14"><rect x="1" y="1" width="16" height="12" fill="none" stroke="#1f2022" stroke-width="2"/><path d="M1 1l8 7 8-7" fill="none" stroke="#1f2022" stroke-width="2"/></svg></span>
        ma@lumavento.dk
      </p>
      <p class="contact-web">www.lumavento.dk</p>
    </div>
  </section>
</body>
</html>
```